STAND OUT BUSINESS CARD REQUIRED

I would like a business card that is going to be different and stand out!

Target Market(s)

Residential market, adults from 28yrs on

Industry/Entity Type

Electrician

Requirements
Must have
• Business name
• my name
• phone number
• email
• web address
• license no.
• abn
• fax no
• logo
Nice to have
• Extra info:
• FREE quotes
• Fixed pricing
• On time guarantee
• Life time labour Guarantee

```html
<!DOCTYPE html>
<html lang="en">
<head>
<meta charset="utf-8">
<title>Bright Spark – Business Card</title>
<link rel="stylesheet" href="https://fonts.googleapis.com/css2?family=Arimo:wght@700&family=Ubuntu:wght@400;500;700&display=swap">
<style>
  :root {
    --page: #ffffff;
    --ink: #111111;
    --card-black: #121212;
    --orange: #f7941d;
    --orange-deep: #e8720c;
    --yellow: #ffd23f;
    --white: #ffffff;
    --gold-light: #ffe27a;
    --gold: #e0a81c;
    --gold-dark: #9a6a06;
    --hero-green: #4f8f3a;
    --hero-red: #c8372d;
  }
  * { margin: 0; padding: 0; box-sizing: border-box; }
  html, body { width: 1200px; height: 873px; overflow: hidden; }
  body { background: var(--page); position: relative; font-family: "Ubuntu", sans-serif; }

  .side-label {
    position: absolute; left: 44px;
    font-family: "Arimo", sans-serif; font-weight: 700; font-size: 50px; color: var(--ink);
  }
  .side-label--front { top: 132px; }
  .side-label--back { top: 540px; }

  .card {
    position: absolute; left: 297px; width: 870px; height: 400px;
    overflow: hidden; border-radius: 4px;
    box-shadow: 0 6px 18px rgba(0,0,0,.35);
  }
  .card--front { top: 33px; background: var(--card-black); }
  .card--back {
    top: 455px;
    background: radial-gradient(ellipse at 50% 45%, #3c3c3c 0%, #1a1a1a 55%, #050505 100%);
  }

  /* front */
  .hero-backdrop { position: absolute; left: 0; top: 0; width: 870px; height: 356px; }
  .hero-illustration {
    position: absolute; left: 560px; top: 30px; width: 250px; height: 230px; border-radius: 40%;
    background: radial-gradient(circle at 45% 55%, var(--hero-green) 0%, var(--hero-red) 55%, rgba(232,114,12,0) 75%);
    opacity: .85;
  }
  .brand-name {
    position: absolute; left: 530px; top: 262px; width: 300px;
    font-weight: 700; font-size: 40px; line-height: 1; color: var(--ink); text-align: center;
  }
  .brand-name small { display: block; font-size: 22px; margin-top: 4px; font-weight: 700; }

  .name-tab {
    position: absolute; left: 0; top: 88px; width: 262px; height: 62px; padding: 6px 0 0 36px;
    background: linear-gradient(90deg, var(--orange-deep), var(--orange));
    border-radius: 0 6px 6px 0;
  }
  .name-tab__name { font-weight: 700; font-size: 27px; color: var(--ink); line-height: 1.05; }
  .name-tab__role { font-weight: 700; font-size: 13px; color: var(--ink); letter-spacing: .5px; }

  .contact-list { position: absolute; left: 36px; top: 182px; list-style: none; font-size: 19px; line-height: 27px; }
  .contact-list li { color: var(--white); }
  .contact-list .label { color: var(--orange); }
  .contact-list .gap { margin-top: 22px; }

  .web-strip {
    position: absolute; left: 0; top: 356px; width: 870px; height: 44px; padding-left: 36px;
    background: linear-gradient(90deg, var(--orange-deep), var(--orange));
    font-size: 19px; font-weight: 500; color: var(--ink); line-height: 44px;
  }

  /* back */
  .guarantees {
    position: absolute; left: 0; top: 110px; width: 870px;
    display: flex; justify-content: center; gap: 70px;
  }
  .guarantee { width: 175px; text-align: center; }
  .guarantee svg { display: block; margin: 0 auto; }
  .guarantee__caption { margin-top: 14px; font-size: 19px; line-height: 1.15; color: var(--white); }
</style>
</head>
<body>
  <div class="side-label side-label--front">Side 1</div>
  <div class="side-label side-label--back">Side 2</div>

  <section class="card card--front">
    <svg class="hero-backdrop" viewBox="0 0 870 356" role="img" aria-label="Orange sunburst background">
      <defs>
        <radialGradient id="burst" cx="0.72" cy="0.3" r="0.6">
          <stop offset="0" stop-color="#ffe066"/>
          <stop offset="0.5" stop-color="#fbb53a"/>
          <stop offset="1" stop-color="#f08c1a"/>
        </radialGradient>
      </defs>
      <path d="M300 0 H870 V356 H420 C520 330 520 250 430 220 C360 200 320 170 300 120 Z" fill="url(#burst)"/>
      <path d="M420 356 C540 320 560 250 470 215 C560 255 560 320 470 356 Z" fill="#121212"/>
    </svg>
    <div class="hero-illustration" role="img" aria-label="Mascot illustration of a caped electrician holding a light bulb"></div>
    <div class="brand-name">BRIGHT SPARK<small>Pty Ltd</small></div>

    <div class="name-tab">
      <div class="name-tab__name">Marcus Hale</div>
      <div class="name-tab__role">DIRECTOR</div>
    </div>

    <ul class="contact-list">
      <li><span class="label">phone:</span> 0400 555 123</li>
      <li><span class="label">fax:</span> 02 5550 1234</li>
      <li class="gap"><span class="label">license no.:</span> 318245K</li>
      <li><span class="label">ABN:</span> 12 345 678 901</li>
    </ul>

    <div class="web-strip">hello@brightsparkpower.com.au &nbsp;|&nbsp; www.brightsparkpower.com.au</div>
  </section>

  <section class="card card--back">
    <div class="guarantees">
      <div class="guarantee">
        <svg width="160" height="160" viewBox="0 0 160 160" aria-hidden="true">
          <defs>
            <radialGradient id="gold" cx="0.4" cy="0.35" r="0.7">
              <stop offset="0" stop-color="#ffe27a"/>
              <stop offset="0.6" stop-color="#e0a81c"/>
              <stop offset="1" stop-color="#9a6a06"/>
            </radialGradient>
          </defs>
          <circle cx="80" cy="80" r="76" fill="url(#gold)"/>
          <circle cx="80" cy="80" r="56" fill="none" stroke="#9a6a06" stroke-width="3"/>
          <text x="80" y="104" text-anchor="middle" font-family="Ubuntu, sans-serif" font-weight="700" font-size="68" fill="#9a6a06">$</text>
        </svg>
        <div class="guarantee__caption">Fixed Pricing<br>Guarantee</div>
      </div>
      <div class="guarantee">
        <svg width="160" height="160" viewBox="0 0 160 160" aria-hidden="true">
          <circle cx="80" cy="80" r="76" fill="url(#gold)"/>
          <circle cx="80" cy="80" r="56" fill="none" stroke="#9a6a06" stroke-width="3"/>
          <circle cx="80" cy="80" r="34" fill="none" stroke="#9a6a06" stroke-width="6"/>
          <path d="M80 58 V80 L96 90" fill="none" stroke="#9a6a06" stroke-width="6" stroke-linecap="round"/>
        </svg>
        <div class="guarantee__caption">On Time<br>Guarantee</div>
      </div>
      <div class="guarantee">
        <svg width="160" height="160" viewBox="0 0 160 160" aria-hidden="true">
          <circle cx="80" cy="80" r="76" fill="url(#gold)"/>
          <circle cx="80" cy="80" r="56" fill="none" stroke="#9a6a06" stroke-width="3"/>
          <g transform="rotate(-45 80 80)" fill="#9a6a06">
            <rect x="74" y="70" width="12" height="48" rx="6"/>
            <path d="M64 52 A18 18 0 1 0 96 52 L96 42 L88 42 L88 58 L72 58 L72 42 L64 42 Z"/>
          </g>
        </svg>
        <div class="guarantee__caption">Lifetime Labour<br>Guarantee</div>
      </div>
    </div>
  </section>
</body>
</html>
```